Redesign of Form/Document Navigation Page

I need a redesign of our document and navigation bar on the left. We want the same navigation bar layout/setup but want the buttons and typography to be simple and matching all over. The form needs to be aesthetically pleasing and fit within the page.

1st attachment is our Direct Deposit and the second is the form continued.

```html
<!DOCTYPE html>
<html lang="en">
<head>
<meta charset="utf-8">
<title>Direct Deposit – Sentinel Crest Security</title>
<link href="https://fonts.googleapis.com/css2?family=Figtree:wght@400;600;700&display=swap" rel="stylesheet">
<style>
  :root{
    --accent:#ebb021;
    --heading:#e9a51c;
    --blue:#2d7ec4;
    --ink:#222;
    --text:#3a3a3a;
    --line:#dcdcdc;
    --page:#f2f2f2;
    --white:#fff;
    --track:#e6e6e6;
  }
  *{box-sizing:border-box;margin:0;padding:0}
  html,body{width:1200px;height:925px;overflow:hidden}
  body{font-family:"Figtree",Arial,sans-serif;background:var(--page);color:var(--text);position:relative}
  .topbar{position:absolute;left:3px;top:0;width:1197px;height:80px;background:var(--white)}
  .brand{position:absolute;left:80px;top:18px;display:flex;align-items:center;gap:8px}
  .brand-mark{width:36px;height:36px;border-radius:50%;background:var(--accent)}
  .brand-name{font-weight:700;color:var(--accent);font-size:19px;line-height:19px;letter-spacing:.2px}
  .topnav{position:absolute;top:30px;display:flex;align-items:center;gap:9px;font-size:13px;color:var(--ink)}
  .topnav.home{left:369px}
  .topnav.help{left:475px}
  .user-btn{position:absolute;left:1014px;top:21px;width:104px;height:35px;border:1px solid var(--line);background:var(--white);display:flex;align-items:center;justify-content:center;gap:10px;font-size:11px;color:var(--ink)}
  .back-btn{position:absolute;left:82px;top:95px;width:138px;height:38px;background:var(--blue);color:var(--white);font-weight:600;font-size:13px;display:flex;align-items:center;gap:13px;padding-left:18px}
  .panel{position:absolute;left:82px;top:146px;width:1036px;height:677px;background:var(--white);border:1px solid var(--line)}
  .sidenav{position:absolute;left:0;top:0;width:250px;height:100%;border-right:1px solid var(--line)}
  .sidenav-item{height:94.5px;border-bottom:1px solid var(--line);display:flex;align-items:center;padding-left:32px;gap:19px;font-size:13px;color:var(--ink)}
  .sidenav-item:last-child{border-bottom:none}
  .sidenav-item.is-active{border-left:3px solid var(--accent);padding-left:29px;color:var(--accent);font-weight:600}
  .sidenav-item svg{width:16px;height:16px;flex:none}
  .scrollbar{position:absolute;right:0;top:0;width:16px;height:100%;background:var(--track)}
  .scroll-thumb{position:absolute;left:0;top:17px;width:16px;height:272px;background:#dadada}
  .scroll-arrow{position:absolute;left:0;width:16px;height:17px;background:#c8c8c8;display:flex;align-items:center;justify-content:center}
  .form{position:absolute;left:0;top:0;width:1018px;height:100%}
  .form > *{position:absolute;white-space:nowrap}
  .form-title{left:287px;top:29px;font-size:16.5px;font-weight:700;color:var(--heading)}
  .form > .terms{left:288px;top:64px;width:687px;font-size:11.2px;line-height:17.6px;text-align:justify;white-space:normal}
  .terms p+p{margin-top:17.6px}
  .label-strong{font-weight:700;font-size:11.5px;color:var(--ink)}
  .label{font-size:11.5px}
  .field{border:1px solid #c9c9c9;background:var(--white);height:42px}
  .accept-btn{left:290px;top:409px;width:207px;height:43px;background:var(--accent);color:var(--white);font-weight:700;font-size:15px;display:flex;align-items:center;gap:16px;padding-left:24px}
  .manager-title{left:292px;top:485px;font-weight:700;font-size:11.5px;color:var(--ink)}
  .manager-box{left:292px;top:509px;width:689px;height:141px;border:1px solid var(--line)}
  .manager-field{position:absolute;width:309px;height:42px;border:1px solid #c9c9c9;font-size:11.5px;display:flex;align-items:center;padding-left:15px}
  .footer{position:absolute;left:0;top:868px;width:1200px;height:57px;background:var(--white);text-align:center;font-size:11px;color:var(--ink);padding-top:25px}
</style>
</head>
<body>
  <header class="topbar">
    <div class="brand"><span class="brand-mark"></span><span class="brand-name">SENTINEL CREST<br>SECURITY</span></div>
    <div class="topnav home">
      <svg width="16" height="14" viewBox="0 0 16 14"><path d="M8 0L0 7h2v7h4V9h4v5h4V7h2z" fill="#222"/></svg>Home
    </div>
    <div class="topnav help">
      <svg width="16" height="16" viewBox="0 0 16 16"><circle cx="8" cy="8" r="7" fill="none" stroke="#222" stroke-width="1.5"/><path d="M6 6.2a2 2 0 1 1 2.8 1.8c-.6.3-.8.7-.8 1.3" fill="none" stroke="#222" stroke-width="1.4"/><circle cx="8" cy="11.6" r=".9" fill="#222"/></svg>Help
    </div>
  </header>
  <div class="user-btn">
    <svg width="14" height="14" viewBox="0 0 14 14"><path d="M4 3a5.5 5.5 0 1 0 6 0" fill="none" stroke="#ebb021" stroke-width="1.5"/><path d="M7 1v6" stroke="#ebb021" stroke-width="1.5"/></svg>Mara Ellis
  </div>

  <div class="back-btn"><svg width="8" height="10" viewBox="0 0 8 10"><path d="M6 1L2 5l4 4" fill="none" stroke="#fff" stroke-width="1.6"/></svg>Back to Profile</div>

  <main class="panel">
    <nav class="sidenav">
      <div class="sidenav-item is-active"><svg viewBox="0 0 16 16"><rect x="1" y="3" width="14" height="10" rx="1" fill="none" stroke="#ebb021" stroke-width="1.5"/><path d="M1 6.5h14" stroke="#ebb021" stroke-width="1.5"/></svg>Direct Deposit</div>
      <div class="sidenav-item"><svg viewBox="0 0 16 16"><circle cx="8" cy="8" r="6.5" fill="none" stroke="#222" stroke-width="1.4"/><circle cx="8" cy="8" r="3.5" fill="none" stroke="#222" stroke-width="1.4"/><circle cx="8" cy="8" r="1.2" fill="#222"/></svg>Change W-4</div>
      <div class="sidenav-item"><svg viewBox="0 0 16 16" fill="#222"><rect x="1" y="1" width="2" height="2"/><rect x="5" y="1" width="2" height="2"/><rect x="9" y="1" width="2" height="2"/><rect x="13" y="1" width="2" height="2"/><rect x="1" y="5" width="2" height="2"/><rect x="13" y="5" width="2" height="2"/><rect x="1" y="9" width="2" height="2"/><rect x="13" y="9" width="2" height="2"/><rect x="1" y="13" width="2" height="2"/><rect x="5" y="13" width="2" height="2"/><rect x="9" y="13" width="2" height="2"/><rect x="13" y="13" width="2" height="2"/></svg>Labour Code</div>
      <div class="sidenav-item"><svg viewBox="0 0 16 16" fill="#222"><circle cx="8" cy="5" r="3.2"/><path d="M2 15c0-3.5 2.7-5 6-5s6 1.5 6 5z"/></svg>Personal Information</div>
      <div class="sidenav-item"><svg viewBox="0 0 16 16"><path d="M8 .8l2.2 4.7 5 .6-3.7 3.4 1 5L8 12l-4.5 2.5 1-5L.8 6.1l5-.6z" fill="#222"/></svg>Appraisal and Review</div>
      <div class="sidenav-item"><svg viewBox="0 0 16 16"><path d="M2 14l.6-3.2 8.2-8.2 2.6 2.6-8.2 8.2z" fill="#222"/></svg>Write Up-Slip</div>
      <div class="sidenav-item"><svg viewBox="0 0 16 16"><path d="M1 12l4-4 3 3 6-6" fill="none" stroke="#222" stroke-width="1.8"/></svg>Employee Performance</div>
    </nav>

    <section class="form">
      <h1 class="form-title">IMPORTANT! Please read and sign before completing and submitting</h1>
      <div class="terms">
        <p>I hereby authorize SENTINEL CREST SECURITY to deposit any amounts owed me, as instructed by my employer, by initiating credit entries to my account at the financial institution (hereinafter "Bank") indicated on this form. Further, I authorize Bank to accept and to credit any credit entries indicated by SENTINEL CREST SECURITY to my account. In the even that SENTINEL CREST SECURITY deposits funds erroneously into my account, I authorize SENTINEL CREST SECURITY to debit my account for an amount not to exceed the original amount of the erroneous credit.</p>
        <p>This authorization is to remain in full force and effect until SENTINEL CREST SECURITY and Bank have received written notice from me of its termination in such time and in such manner as to afford SENTINEL CREST SECURITY and Bank reasonable opportunity to act on it.</p>
      </div>
      <div class="label-strong" style="left:290px;top:245px">Employee Name</div>
      <div class="label" style="left:290px;top:264px">Employee Signature</div>
      <div class="field" style="left:288px;top:299px;width:208px"></div>
      <div class="field" style="left:288px;top:352px;width:208px"></div>
      <div class="label-strong" style="left:666px;top:334px">Sign Date</div>
      <div class="field" style="left:737px;top:324px;width:207px"></div>
      <div class="accept-btn"><svg width="16" height="12" viewBox="0 0 16 12"><path d="M1 6l4.5 4.5L15 1" fill="none" stroke="#fff" stroke-width="1.8"/></svg>Accept Document</div>
      <div class="manager-title">ONLY PAYROLL MANAGER SIGNS BELOW</div>
      <div class="manager-box">
        <div class="manager-field" style="left:23px;top:23px">Company Name</div>
        <div class="manager-field" style="left:355px;top:23px;padding-left:22px">Comments</div>
        <div class="manager-field" style="left:23px;top:78px">Employee File Number</div>
      </div>
    </section>

    <div class="scrollbar">
      <div class="scroll-thumb"></div>
      <div class="scroll-arrow" style="top:0"><svg width="10" height="6" viewBox="0 0 10 6"><path d="M1 5l4-4 4 4" fill="none" stroke="#fff" stroke-width="1.5"/></svg></div>
      <div class="scroll-arrow" style="bottom:0"><svg width="10" height="6" viewBox="0 0 10 6"><path d="M1 1l4 4 4-4" fill="none" stroke="#fff" stroke-width="1.5"/></svg></div>
    </div>
  </main>

  <footer class="footer">Copyrights @ 2016 All Rights Reserved</footer>
</body>
</html>
```